Every Shelf Set Neatly or ESN Organized needs a business card design. ESN Organized is a professi

We need a business card design that is clean, sharp and conveys a sense of organization. I already have a logo.

Target Market(s)

Families (specifically mothers), small business owners, parents, seniors

Industry/Entity Type

Business

Contact Information for Business Card

My website is www.esnorganized-example.com and my Facebook page is http://www.sociallink-example.com/everyshelfsetneatly. The phone number is 418-552-7094 and I want to be listed as Lorna M. Pelham, Owner

Requirements
Must have
• My logo.

```html
<!DOCTYPE html>
<html lang="en">
<head>
<meta charset="utf-8">
<title>ESN Organized – Business Card</title>
<link rel="stylesheet" href="https://fonts.googleapis.com/css2?family=Montserrat:wght@400;500&family=Roboto:wght@400;500&display=swap">
<style>
  :root {
    --page-bg: #e9e9ea;
    --card-bg: #ffffff;
    --brand-blue: #1d84e0;
    --brand-blue-soft: #3e98e8;
    --ink: #1d1d1d;
    --ink-soft: #3a3a3a;
    --on-blue: #ffffff;
  }
  * { box-sizing: border-box; margin: 0; padding: 0; }
  html, body { width: 1200px; height: 950px; overflow: hidden; }
  body {
    background: var(--page-bg);
    font-family: "Montserrat", sans-serif;
    color: var(--ink);
    position: relative;
  }
  .card {
    position: absolute;
    left: 250px;
    width: 700px;
    height: 400px;
    background: var(--card-bg);
    box-shadow: 0 6px 18px rgba(0,0,0,0.18);
    overflow: hidden;
  }
  .card--front { top: 45px; }
  .card--back { top: 505px; }

  .brand-name {
    font-family: "Montserrat", sans-serif;
    font-weight: 500;
    color: var(--brand-blue);
    font-size: 48px;
    letter-spacing: 3px;
    white-space: nowrap;
  }
  .card--front .brand-name {
    position: absolute;
    left: 120px;
    top: 120px;
  }
  .website-line {
    position: absolute;
    left: 160px;
    top: 230px;
    font-size: 17px;
    letter-spacing: 6px;
    color: var(--ink-soft);
  }

  .card--back .brand-name {
    position: absolute;
    left: 70px;
    top: 60px;
    font-size: 42px;
  }
  .contact-list {
    position: absolute;
    left: 40px;
    top: 200px;
    list-style: none;
    font-family: "Roboto", sans-serif;
    font-size: 19px;
    color: var(--ink-soft);
  }
  .contact-item {
    display: flex;
    align-items: center;
    gap: 9px;
    height: 28px;
  }
  .contact-icon { width: 16px; height: 16px; flex: none; }

  .owner-band {
    position: absolute;
    right: 0;
    top: 0;
    width: 170px;
    height: 400px;
    background: var(--brand-blue);
    border-top-left-radius: 85px;
  }
  .owner-label {
    position: absolute;
    left: 50%;
    top: 58%;
    transform: translate(-50%, -50%) rotate(-90deg);
    text-align: center;
    color: var(--on-blue);
    font-family: "Roboto", sans-serif;
    white-space: nowrap;
  }
  .owner-name { font-size: 25px; font-weight: 500; letter-spacing: 0.5px; }
  .owner-role { font-size: 17px; font-weight: 500; margin-top: 8px; letter-spacing: 0.5px; }
</style>
</head>
<body>
  <section class="card card--front" aria-label="Card front">
    <div class="brand-name">ESN Organized</div>
    <p class="website-line">www.esnorganized-example.com</p>
  </section>

  <section class="card card--back" aria-label="Card back">
    <div class="brand-name">ESN Organized</div>

    <ul class="contact-list">
      <li class="contact-item">
        <svg class="contact-icon" viewBox="0 0 16 16" aria-hidden="true">
          <circle cx="8" cy="8" r="8" fill="var(--brand-blue)"/>
          <path d="M5.2 4.2l1.6-.4.9 2-1 .8a5 5 0 0 0 2.7 2.7l.8-1 2 .9-.4 1.6c-3.6.4-7-3-6.6-6.6z" fill="#fff"/>
        </svg>
        <span>418-552-7094</span>
      </li>
      <li class="contact-item">
        <svg class="contact-icon" viewBox="0 0 16 16" aria-hidden="true">
          <circle cx="8" cy="8" r="8" fill="var(--brand-blue)"/>
          <circle cx="8" cy="8" r="4.5" fill="none" stroke="#fff" stroke-width="1.2"/>
          <path d="M3.5 8h9M8 3.5c-2 2.5-2 6.5 0 9M8 3.5c2 2.5 2 6.5 0 9" fill="none" stroke="#fff" stroke-width="1"/>
        </svg>
        <span>www.esnorganized-example.com</span>
      </li>
      <li class="contact-item">
        <svg class="contact-icon" viewBox="0 0 16 16" aria-hidden="true">
          <rect width="16" height="16" rx="2" fill="var(--brand-blue)"/>
        </svg>
        <span>everyshelfsetneatly</span>
      </li>
    </ul>

    <div class="owner-band">
      <div class="owner-label">
        <div class="owner-name">LORNA M. PELHAM</div>
        <div class="owner-role">OWNER</div>
      </div>
    </div>
  </section>
</body>
</html>
```